Quran Jar

So I need help designing bespoke jars which will contain religious quotes.

So there will be three jars in total sold either individually or in two or as a three.

Each Jar will have different contents and preferably a different colour scheme.

I want the packaging to be customised with my branding and logo and to make the product stand out I am thinking of packing it further in a cotton bag with my branding.

```html
<!DOCTYPE html>
<html lang="en">
<head>
<meta charset="utf-8">
<title>Quiet Lantern – Jar Packaging</title>
<link rel="stylesheet" href="https://fonts.googleapis.com/css2?family=Montserrat:wght@300;400;500&display=swap">
<style>
  :root {
    --bg-light: #f1f1f1;
    --bg-panel: #dcdcdc;
    --gold: #8a7424;
    --gold-dark: #6f5c18;
    --gold-light: #d9c45a;
    --gold-text: #e0c978;
    --brand-gold: #8a6d1c;
    --white-label: #f4f4f4;
    --green: #1f6442;
    --green-dark: #164b30;
    --c-yellow: #f2c94c;
    --c-blue: #8ecae6;
    --c-purple: #b78be0;
    --c-green: #8fd18f;
    --c-orange: #f0a040;
    --c-amber: #e8823a;
    --c-pink: #f4b6c2;
    --c-red: #d0202a;
  }
  * { box-sizing: border-box; margin: 0; padding: 0; }
  html, body { width: 1200px; height: 505px; overflow: hidden; }
  body {
    position: relative;
    background: var(--bg-light);
    font-family: "Montserrat", sans-serif;
  }
  ul { list-style: none; }

  .box-stage {
    position: absolute; left: 785px; top: 0; width: 415px; height: 505px;
    background: linear-gradient(180deg, #e8e8e8, var(--bg-panel));
  }

  .brand-dot { display: block; border-radius: 50%; }

  /* Jar labels */
  .jar-label {
    position: absolute; top: 235px; width: 144px; height: 110px;
    display: flex; flex-direction: column; align-items: center;
    padding-top: 32px;
  }
  .jar-label--hadith { left: 97px; background: var(--gold); color: #f3f0e6; }
  .jar-label--dua { left: 270px; background: var(--white-label); color: #4a4a4a; box-shadow: 0 0 0 1px #e2e2e2 inset; }

  .jar-label .brand-dot { width: 11px; height: 11px; margin-bottom: 4px; }
  .jar-label--hadith .brand-dot { background: var(--gold-text); }
  .jar-label--dua .brand-dot { background: var(--brand-gold); }

  .brand-name { font-weight: 400; font-size: 8px; line-height: 9px; white-space: nowrap; }
  .jar-label--hadith .brand-name { color: var(--gold-text); }
  .jar-label--dua .brand-name { color: var(--brand-gold); }
  .brand-tagline { font-size: 2.2px; line-height: 3px; letter-spacing: 0.8px; text-transform: uppercase; opacity: .8; }

  .jar-title { font-weight: 300; font-size: 13px; line-height: 13px; margin-top: 3px; letter-spacing: 0.3px; }
  .jar-subtitle { font-weight: 300; font-size: 6.5px; line-height: 7px; }

  .mood-strip { display: flex; width: 138px; margin-top: 8px; }
  .mood { flex: 1; font-size: 2.2px; line-height: 3px; text-transform: uppercase; text-align: center; }
  .mood::before { content: ""; display: block; height: 3px; margin-bottom: 0.5px; }
  .mood--happy::before { background: var(--c-yellow); }
  .mood--sad::before { background: var(--c-blue); }
  .mood--anxious::before { background: var(--c-purple); }
  .mood--grateful::before { background: var(--c-green); }
  .mood--patient::before { background: var(--c-orange); }
  .mood--hope::before { background: var(--c-amber); }
  .mood--forgive::before { background: var(--c-pink); }
  .mood--love::before { background: var(--c-red); }

  .jar-note { font-size: 2.2px; line-height: 3px; width: 118px; text-align: center; margin-top: 2px; opacity: .75; }

  /* Cotton pouch */
  .pouch {
    position: absolute; left: 513px; top: 174px; width: 207px; height: 203px;
    background: radial-gradient(ellipse at 50% 45%, var(--green) 0%, var(--green-dark) 100%);
    display: flex; flex-direction: column; align-items: center;
    padding-top: 110px;
  }
  .pouch .brand-dot { width: 17px; height: 17px; background: var(--gold-light); margin-bottom: 5px; }
  .pouch .brand-name { color: var(--gold-light); font-size: 9.5px; line-height: 11px; }
  .pouch .brand-tagline { color: var(--gold-light); font-size: 2.6px; }

  /* Gift box lid */
  .gift-box-lid {
    position: absolute; left: 858px; top: 205px; width: 262px; height: 118px;
    background: linear-gradient(120deg, var(--gold-dark), #b3992f 55%, var(--gold-light));
    display: flex; flex-direction: column; align-items: center;
    padding-top: 29px;
    color: #efe3b0; overflow: hidden;
  }
  .gift-box-lid::after {
    content: ""; position: absolute; right: 0; top: 0;
    border-top: 26px solid #f7f7f7; border-left: 70px solid transparent;
  }
  .gift-box-lid .brand-dot { width: 8px; height: 8px; background: #efe3b0; margin-bottom: 3px; }
  .gift-box-lid .brand-name { font-size: 7px; line-height: 8px; color: #efe3b0; }
  .gift-box-lid .brand-tagline { font-size: 2px; }
  .box-contents { display: flex; align-items: center; gap: 8px; margin-top: 9px; }
  .box-item { display: flex; flex-direction: column; align-items: center; }
  .box-item b { font-weight: 300; font-size: 8px; line-height: 9px; }
  .box-item small { font-weight: 300; font-size: 4px; line-height: 5px; }
  .box-divider { width: 1px; height: 15px; background: #efe3b0; opacity: .7; }
</style>
</head>
<body>
  <div class="box-stage"></div>

  <section class="jar-label jar-label--hadith">
    <span class="brand-dot"></span>
    <p class="brand-name">Quiet Lantern</p>
    <p class="brand-tagline">Words for every day</p>
    <h1 class="jar-title">HADITH</h1>
    <p class="jar-subtitle">JAR</p>
    <ul class="mood-strip">
      <li class="mood mood--happy">Happy</li><li class="mood mood--sad">Sad</li>
      <li class="mood mood--anxious">Anxious</li><li class="mood mood--grateful">Grateful</li>
      <li class="mood mood--patient">Patience</li><li class="mood mood--hope">Hope</li>
      <li class="mood mood--forgive">Forgive</li><li class="mood mood--love">Love</li>
    </ul>
    <p class="jar-note">Draw a slip when your heart needs it and read the words slowly, then fold it back for another day.</p>
  </section>

  <section class="jar-label jar-label--dua">
    <span class="brand-dot"></span>
    <p class="brand-name">Quiet Lantern</p>
    <p class="brand-tagline">Words for every day</p>
    <h1 class="jar-title">DUA</h1>
    <p class="jar-subtitle">JAR</p>
    <ul class="mood-strip">
      <li class="mood mood--happy">Happy</li><li class="mood mood--sad">Sad</li>
      <li class="mood mood--anxious">Anxious</li><li class="mood mood--grateful">Grateful</li>
      <li class="mood mood--patient">Patience</li><li class="mood mood--hope">Hope</li>
      <li class="mood mood--forgive">Forgive</li><li class="mood mood--love">Love</li>
    </ul>
    <p class="jar-note">Draw a slip when your heart needs it and read the words slowly, then fold it back for another day.</p>
  </section>

  <section class="pouch">
    <span class="brand-dot"></span>
    <p class="brand-name">Quiet Lantern</p>
    <p class="brand-tagline">Words for every day</p>
  </section>

  <section class="gift-box-lid">
    <span class="brand-dot"></span>
    <p class="brand-name">Quiet Lantern</p>
    <p class="brand-tagline">Words for every day</p>
    <div class="box-contents">
      <div class="box-item"><b>HADITH</b><small>JAR</small></div>
      <span class="box-divider"></span>
      <div class="box-item"><b>DUA</b><small>JAR</small></div>
    </div>
  </section>
</body>
</html>
```